Bright bears day nursery qrp limited

we would like create a website that can be updated by us easily as we have regular changes to what we provide and need. we would like something that is classy but also appealing from a child's aspect. we would be looking to add our own logo and our kinderwatch logo both attached, if you guys can create it and we will work with the preferred choice to add all the text.
We would like the links to family pathways, kinderwatch report and our chatterbook feed on the front page

we are looking for a website for our childcare business we have 2 nurseries that we would like one website.
showing our opening hours, price list, policies etc as well as photos, description of our day, staff photos and their training accreditation's.

Target Market(s)

Families

Industry/Entity Type

Childcare

Number of Pages Required

5+ page

Font styles to use
Serif

Colors

Designer to choose colors to be used in the design.

Requirements
Must have
• links to social media and other websites, photographs, links to download registration forms etc, parents able to leave reviews. google maps link, job opportunities
Nice to have
• facilities to take payments

```html
<!DOCTYPE html>
<html lang="en">
<head>
<meta charset="utf-8">
<title>Bright Bears Day Nursery</title>
<link href="https://fonts.googleapis.com/css2?family=Roboto:wght@300;400;500;700&family=Roboto+Condensed:wght@400;700&display=swap" rel="stylesheet">
<style>
:root{
  --pink:#d4096f;
  --blue:#1c9fdc;
  --cyan:#16b2e6;
  --sky:#e4f2fb;
  --green:#58b43c;
  --ink:#2b2b2b;
  --grey:#666;
  --line:#e5e5e5;
  --foot:#f4f4f4;
  --white:#fff;
}
*{box-sizing:border-box;margin:0;padding:0}
html,body{width:1200px;height:3403px;overflow:hidden}
body{position:relative;background:var(--white);font-family:'Roboto',sans-serif;color:var(--ink)}
.abs{position:absolute}
.heading{font-family:'Roboto Condensed',sans-serif;font-weight:400;text-transform:uppercase;color:var(--ink);font-size:31px;letter-spacing:.5px}
.center{text-align:center;left:0;width:1200px}
p.body{font-size:12.5px;line-height:20px;color:var(--grey)}

/* header */
.site-header{top:0;left:0;width:1200px;height:120px;background:var(--white);z-index:3}
.brand{left:60px;top:-50px;width:230px;height:230px;border-radius:50%;background:var(--white);z-index:4;display:flex;align-items:center;justify-content:center;padding-top:70px}
.brand span{font-family:'Roboto',sans-serif;font-weight:700;color:var(--blue);font-size:20px;line-height:24px;text-align:center;text-transform:uppercase}
.contact-phone{left:800px;top:28px;font-size:15px;color:#444;display:flex;align-items:center;gap:10px}
.socials{left:1020px;top:26px;display:flex;gap:5px}
.socials i{display:block;width:22px;height:22px;border-radius:50%;background:var(--blue)}
.socials i:nth-child(2){background:var(--pink)}
.main-nav{right:62px;top:84px;display:flex;gap:26px;font-size:12.5px;text-transform:uppercase;color:#333}
.main-nav .active{color:var(--pink)}

/* hero */
.hero{top:120px;left:0;width:1200px;height:556px;background:linear-gradient(120deg,#d9c6b2 0%,#b8a594 35%,#7d8fb0 60%,#3f74c4 100%)}
.hero-card{left:118px;top:313px;width:347px;height:227px;background:rgba(212,9,111,.85);padding:20px 22px;z-index:2}
.hero-card h1{font-family:'Roboto Condensed',sans-serif;font-weight:700;color:#fff;font-size:39px;line-height:42px;text-transform:uppercase}
.hero-card p{color:#fff;font-size:13px;line-height:19px;margin-top:12px}
.btn-ghost{display:inline-flex;align-items:center;gap:6px;border:1.5px solid #fff;color:#fff;font-size:11px;text-transform:uppercase;padding:6px 14px;border-radius:3px;margin-top:14px}
.slider-arrow{top:398px;width:36px;height:36px;border-radius:50%;background:rgba(0,0,0,.55);z-index:2;display:flex;align-items:center;justify-content:center}

/* description */
.btn-solid{background:var(--cyan);color:#fff;font-size:14px;font-weight:500;text-transform:uppercase;padding:11px 20px;border-radius:3px}

/* price */
.price{top:990px;left:0;width:1200px;height:644px;background:var(--blue)}
.price-title{color:#fff}
.price-sub{color:#fff;font-size:21px;font-weight:300}
.card{background:#fff;border-radius:12px;box-shadow:0 6px 18px rgba(0,0,0,.15);overflow:hidden}
.card-head{background:var(--pink);color:#fff;font-family:'Roboto Condensed',sans-serif;font-weight:700;font-size:21px;display:flex;align-items:center;justify-content:center}
.row{position:absolute;left:0;width:100%;display:flex;align-items:center;justify-content:center;text-align:center;font-size:13px;line-height:19px;color:#555;border-top:1px solid var(--line)}
.pink-txt{color:var(--pink)}

/* staff */
.staff{top:1634px;left:0;width:1200px;height:521px;background:var(--sky)}
.rule{width:46px;height:2px;background:var(--cyan)}
.member{width:220px;text-align:center}
.member .ring{width:194px;height:194px;margin:0 auto;border-radius:50%;border:2px dashed #9fc4dd;padding:7px}
.member .photo{width:100%;height:100%;border-radius:50%;background:radial-gradient(circle at 50% 40%,#c8b4a2,#6b5a50 70%,#3b3b3b)}
.member h3{font-weight:400;font-size:19px;margin-top:16px}
.member small{display:block;font-size:11px;color:#444;margin-top:6px}

/* blog */
.post-img{width:172px;height:134px}
.post-title{font-size:15px;color:#333}
.post-meta{font-size:10.5px;color:var(--blue);text-transform:uppercase;margin-top:12px}
.feed{left:703px;top:2295px;width:397px;height:318px;border:1px solid #ddd;background:#fff}

/* accreditation */
.training{top:2700px;left:0;width:1200px;height:340px;background:linear-gradient(90deg,rgba(88,180,60,.92),rgba(96,186,66,.88)),linear-gradient(90deg,#8f7a5f,#5c8b4a)}
.training h2{color:#fff;font-family:'Roboto Condensed',sans-serif;font-weight:700;font-size:40px;text-transform:uppercase}

/* footer */
.footer{top:3040px;left:0;width:1200px;height:294px;background:var(--foot)}
.foot-head{font-size:16px;text-transform:uppercase;color:#333;letter-spacing:.3px}
.foot-txt{font-size:12px;line-height:21px;color:#555}
.bottom-bar{top:3334px;left:0;width:1200px;height:69px;background:#fff;border-top:1px solid var(--line);font-size:11.5px;color:#444}
</style>
</head>
<body>

<!-- header -->
<header class="abs site-header">
  <div class="abs contact-phone">
    <svg width="18" height="18" viewBox="0 0 24 24"><path fill="#555" d="M6.6 10.8a15 15 0 0 0 6.6 6.6l2.2-2.2c.3-.3.7-.4 1-.2 1.1.4 2.3.6 3.6.6.6 0 1 .4 1 1V20c0 .6-.4 1-1 1A17 17 0 0 1 3 4c0-.6.4-1 1-1h3.5c.6 0 1 .4 1 1 0 1.3.2 2.5.6 3.6.1.3 0 .7-.2 1z"/></svg>
    Phone : 01632 960 418
  </div>
  <div class="abs socials"><i></i><i></i><i></i></div>
  <nav class="abs main-nav">
    <span class="active">Home</span><span>About us</span><span>Our price</span><span>Our staff</span><span>Services</span><span>Contact us</span>
  </nav>
</header>
<div class="abs brand"><span>Bright Bears<br>Day Nursery</span></div>

<!-- hero -->
<section class="abs hero" role="img" aria-label="Photo of a carer with two children building with colourful toy blocks"></section>
<div class="abs hero-card">
  <h1>Bright Bears Day Nursery</h1>
  <p>Sed ut perspiciatis unde omnis iste natus error sit voluptatem accusantium doloremque</p>
  <span class="btn-ghost">Read more
    <svg width="11" height="11" viewBox="0 0 12 12"><circle cx="6" cy="6" r="6" fill="#fff"/><path d="M5 3.5 7.5 6 5 8.5" stroke="#d4096f" stroke-width="1.5" fill="none"/></svg>
  </span>
</div>
<div class="abs slider-arrow" style="left:32px"><svg width="12" height="14" viewBox="0 0 12 14"><path d="M8 2 3 7l5 5" stroke="#fff" stroke-width="2.5" fill="none"/></svg></div>
<div class="abs slider-arrow" style="left:1130px"><svg width="12" height="14" viewBox="0 0 12 14"><path d="M4 2l5 5-5 5" stroke="#fff" stroke-width="2.5" fill="none"/></svg></div>

<!-- description -->
<h2 class="abs heading center" style="top:740px">Description of our day</h2>
<p class="abs body" style="top:798px;left:165px;width:870px;text-align:center">Lorem ipsum dolor sit amet, consectetur adipiscing elit, sed do eiusmod tempor incididunt ut labore et dolore magna aliqua. Ut enim ad minim veniam, quis nostrud exercitation ullamco laboris nisi ut aliquip ex ea commodo consequat. Duis aute irure dolor in reprehenderit in voluptate velit esse cillum dolore eu fugiat nulla pariatur. Excepteur sint occaecat cupidatat non proident, sunt in culpa qui officia deserunt mollit anim id est laborum</p>
<div class="abs" style="top:888px;left:0;width:1200px;text-align:center"><span class="btn-solid">Read more</span></div>

<!-- price -->
<section class="abs price">
  <svg class="abs" style="top:-2px;left:0" width="1200" height="40" viewBox="0 0 1200 40" preserveAspectRatio="none">
    <path d="M0 0H1200V20C1100 40 1000 0 900 14C800 28 700 4 600 12C500 20 400 2 300 16C200 30 100 4 0 20Z" fill="#fff"/>
  </svg>
</section>
<h2 class="abs heading center price-title" style="top:1052px">Our price</h2>
<div class="abs center price-sub" style="top:1103px">New price list from 1 st April 2017</div>

<div class="abs card" style="left:195px;top:1195px;width:810px;height:375px">
  <div class="card-head" style="height:60px"></div>
  <div style="position:absolute;left:0;top:60px;width:259px;height:315px">
    <div class="row" style="top:0;height:75px;border-top:none">Half day<br>8am-1pm or 1pm-6pm</div>
    <div class="row" style="top:75px;height:75px">Full day<br>(7.30-6pm)</div>
    <div class="row" style="top:150px;height:75px">Full time<br>Mon- Fri 7.30-6pm</div>
    <div class="row" style="top:225px;height:90px">Full time funded children<br>3+ years old+</div>
  </div>
  <div style="position:absolute;left:545px;top:0;width:265px;height:375px">
    <div class="card-head" style="height:60px">2-5'S</div>
    <div class="row" style="top:60px;height:75px;border-top:none">£25</div>
    <div class="row" style="top:135px;height:75px">£38</div>
    <div class="row" style="top:210px;height:75px">£161<br>(Funded children in holidays)</div>
    <div class="row" style="top:285px;height:90px">£130<br>During term time</div>
  </div>
</div>
<div class="abs card" style="left:454px;top:1168px;width:286px;height:420px;z-index:2;box-shadow:0 8px 24px rgba(0,0,0,.25)">
  <div class="card-head" style="height:92px">UNDER 2'S</div>
  <div class="row" style="top:92px;height:75px;border-top:none"><span class="pink-txt">£26</span></div>
  <div class="row" style="top:167px;height:75px"><span class="pink-txt">£40</span></div>
  <div class="row" style="top:242px;height:75px"><span class="pink-txt">£168</span></div>
  <div class="row" style="top:317px;height:90px"><span class="pink-txt">xxxxxxxxxxx</span></div>
</div>

<!-- staff -->
<section class="abs staff"></section>
<h2 class="abs heading center" style="top:1731px">Our staff</h2>
<div class="abs rule" style="top:1787px;left:577px"></div>
<div class="abs member" style="left:103px;top:1837px"><div class="ring"><div class="photo" role="img" aria-label="Staff portrait"></div></div><h3>Marla Quentin</h3><small>Co-founder and CEO</small></div>
<div class="abs member" style="left:359px;top:1837px"><div class="ring"><div class="photo" role="img" aria-label="Staff portrait"></div></div><h3>Marla Quentin</h3><small>Co-founder and CEO</small></div>
<div class="abs member" style="left:616px;top:1837px"><div class="ring"><div class="photo" role="img" aria-label="Staff portrait"></div></div><h3>Marla Quentin</h3><small>Co-founder and CEO</small></div>
<div class="abs member" style="left:872px;top:1837px"><div class="ring"><div class="photo" role="img" aria-label="Staff portrait"></div></div><h3>Marla Quentin</h3><small>Co-founder and CEO</small></div>

<!-- blog -->
<h2 class="abs heading" style="top:2222px;left:98px;font-size:29px">Latest blog</h2>
<div class="abs post-img" style="left:100px;top:2309px;background:linear-gradient(135deg,#4aa7c9,#c5563f 55%,#e7c7a0)" role="img" aria-label="Blog photo of a playroom with toys"></div>
<div class="abs" style="left:295px;top:2305px;width:345px">
  <div class="post-title">Nemo Enim Ipsam Voluptatem</div>
  <div class="post-meta">3 minutes ago &nbsp;/&nbsp; 0 comments</div>
  <p class="body" style="margin-top:8px">Lorem ipsum dolor sit amet, consectetur adipiscing elit, sed do eiusmod tempor incididunt ut labore et dolore magna aliqua. Ut enim ad minim veniam, quis nostrud</p>
</div>
<div class="abs" style="left:100px;top:2458px;width:540px;height:1px;background:var(--line)"></div>
<div class="abs post-img" style="left:100px;top:2474px;background:linear-gradient(135deg,#5a2a1f,#b8a090 55%,#efe7de)" role="img" aria-label="Blog photo of children's costumes on display"></div>
<div class="abs" style="left:295px;top:2470px;width:345px">
  <div class="post-title">Nemo Enim Ipsam Voluptatem</div>
  <div class="post-meta">3 minutes ago &nbsp;/&nbsp; 0 comments</div>
  <p class="body" style="margin-top:8px">Lorem ipsum dolor sit amet, consectetur adipiscing elit, sed do eiusmod tempor incididunt ut labore et dolore magna aliqua. Ut enim ad minim veniam, quis nostrud</p>
</div>

<!-- chatterbook feed -->
<h2 class="abs heading" style="top:2222px;left:703px;font-size:29px">Follow us on Chatterbook</h2>
<div class="abs feed">
  <div style="height:135px;background:linear-gradient(90deg,#22324a,#3b4e6b)" role="img" aria-label="Nursery page cover image"></div>
  <div class="abs" style="left:96px;top:18px;color:#fff;font-size:15px;font-weight:500">BRIGHT BEARS DAY NURSERY</div>
  <div class="abs" style="left:96px;top:40px;color:#fff;font-size:11px">8 likes</div>
  <div class="abs" style="left:14px;top:12px;width:70px;height:70px;background:#fff;border:1px solid #ccc"></div>
  <div class="abs" style="left:14px;top:94px;background:#f4f4f4;border:1px solid #ccc;font-size:11px;padding:3px 8px;color:#333">Like Page</div>
  <div class="abs" style="left:318px;top:94px;background:#f4f4f4;border:1px solid #ccc;font-size:11px;padding:3px 8px;color:#333">Share</div>
  <div class="abs" style="left:14px;top:148px;width:368px;height:120px;background:linear-gradient(90deg,#b69a83,#d9cfc4 40%,#8d8f95 70%,#c7b9a8)" role="img" aria-label="Grid of recent page photos"></div>
  <div class="abs" style="left:0;top:282px;width:100%;border-top:1px solid #ddd;padding:10px 14px;font-size:11.5px;color:#444;display:flex;align-items:center;gap:8px"><i style="display:block;width:12px;height:12px;background:var(--blue)"></i>Chatterbook social plugin</div>
</div>

<!-- accreditation -->
<section class="abs training" role="img" aria-label="Faded photo of a child at play behind a green overlay"></section>
<h2 class="abs center" style="top:2793px;color:#fff;font-family:'Roboto Condensed',sans-serif;font-weight:700;font-size:40px">TRAINING ACCREDITATION'S</h2>
<p class="abs body" style="top:2850px;left:190px;width:820px;text-align:center;color:#fff">Sed ut perspiciatis unde omnis iste natus error sit voluptatem accusantium doloremque laudantium, totam rem aperiam, eaque ipsa quae ab illo inventore veritatis et quasi architecto beatae vitae dicta sunt explicabo. Nemo enim ipsam voluptatem quia voluptas</p>
<div class="abs" style="top:2915px;left:0;width:1200px;text-align:center"><span class="btn-ghost" style="font-size:13px;padding:10px 22px;border-radius:20px">Read more
  <svg width="12" height="12" viewBox="0 0 12 12"><circle cx="6" cy="6" r="6" fill="#fff"/><path d="M5 3.5 7.5 6 5 8.5" stroke="#58b43c" stroke-width="1.5" fill="none"/></svg></span></div>

<!-- footer -->
<footer class="abs footer">
  <div class="abs" style="left:104px;top:62px;font-size:29px;line-height:32px;color:#333;font-weight:400">Family<br>Pathways</div>
  <div class="abs" style="left:100px;top:148px;width:100px;height:88px;background:#24306a;border-radius:4px"></div>
  <div class="abs" style="left:210px;top:148px;width:110px;height:88px;background:#24306a;border-radius:4px;border-right:8px solid #f1c232"></div>

  <div class="abs foot-head" style="left:410px;top:65px">Sign up for newsletter</div>
  <p class="abs foot-txt" style="left:410px;top:96px;width:250px">Excepteur sint occaecat cupidatat non proident, sunt in culpa qui officia deserunt</p>
  <div class="abs" style="left:410px;top:160px;width:245px;height:40px;background:#fff;border:1px solid #ddd;font-size:11px;color:#777;padding:12px 10px">Enter email</div>
  <div class="abs" style="left:410px;top:212px;background:var(--pink);color:#fff;font-size:12px;text-transform:uppercase;padding:8px 14px">Subscription</div>

  <div class="abs foot-head" style="left:714px;top:65px">Contact us</div>
  <div class="abs foot-txt" style="left:714px;top:98px;display:flex;gap:10px">
    <svg width="12" height="16" viewBox="0 0 12 16"><path d="M6 0a6 6 0 0 0-6 6c0 4.5 6 10 6 10s6-5.5 6-10a6 6 0 0 0-6-6zm0 8.5A2.5 2.5 0 1 1 6 3.5a2.5 2.5 0 0 1 0 5z" fill="#777"/></svg>
    <span>Bright Bears Day Nursery<br>14 Meadow Lane, Ashbury,<br>AB1 2CD</span>
  </div>
  <div class="abs foot-txt" style="left:714px;top:170px;display:flex;gap:10px;align-items:center">
    <svg width="13" height="13" viewBox="0 0 24 24"><path fill="#777" d="M6.6 10.8a15 15 0 0 0 6.6 6.6l2.2-2.2c.3-.3.7-.4 1-.2 1.1.4 2.3.6 3.6.6.6 0 1 .4 1 1V20c0 .6-.4 1-1 1A17 17 0 0 1 3 4c0-.6.4-1 1-1h3.5c.6 0 1 .4 1 1 0 1.3.2 2.5.6 3.6.1.3 0 .7-.2 1z"/></svg>Phone: &nbsp;01632 960 552</div>
  <div class="abs foot-txt" style="left:714px;top:205px;display:flex;gap:10px;align-items:center">
    <svg width="13" height="10" viewBox="0 0 14 10"><rect width="14" height="10" fill="#777"/><path d="M0 0l7 5 7-5" stroke="#f4f4f4" fill="none"/></svg>hello@brightbearsqrp.example</div>

  <div class="abs foot-head" style="left:973px;top:60px">Opening hours</div>
  <p class="abs foot-txt" style="left:973px;top:96px;font-size:11.5px">Monday-Thursday:<br>10:00 a.m.- 1:00 p.m<br>Tuesday-Friday:<br>9:30 a.m. - 5:00 p.m</p>
</footer>
<div class="abs bottom-bar">
  <span class="abs" style="left:98px;top:26px">©2017 Bright Bears Day Nursery, All Rights Reserved.</span>
  <span class="abs" style="left:945px;top:26px">Policy / About Us / Contact Us</span>
</div>

</body>
</html>
```